Business Cards for new orthopaedic surgery practice

My husband and I are starting our own orthopaedic surgery practice. We are looking for a business card that is uniform, but one will have my name/title and the other will have his. You can just create one design with my name on it for now. But when I choose your design as the winning design I will ask that you add another copy with his name/title.

We are looking for classy, simple, elite all in one. We like dark blues/a little gold/yellow. Something that goes with our logo. We want our logo incorporated. Here is all the info you need:
Business name: RV Bone & Vitality Center
Location: 38517 North Willowmere Ave
Brightwater Cove, FL 33498
Phone: 954-218-4063
Fax: 954-582-7341
Email: info@myrvbonecare.example

Names: Lydia Vance, M.D.
Board Certified Hand and Upper Extremity Surgeon

Ebo Dansu, M.D.
Board Certified Hip & Knee Replacement/General Orthopaedic Surgeon

Can decide what you want to put on the back. Maybe a slogan:
Grounded in Care. Centered on You

I am just going to upload our logo. The only thing is if we select you as the winning design, the location, and phone numbers may change. We will need your help to update that once fully solidified.

Industry/Entity Type

Medical

Contact Information for Business Card

Colors
0054AA
0677BA
7BADD7
CADEEF
E8F1F8
0094D4
00A9DD
6FCCEA
C7EBF8
E9F6FB

Requirements
Must have
• class, appeal,
Should not have
• We want to air on the side of masculine if we are looking at masculine vs. feminine feel. But we still want it classy, sophisticated, and something we will love

```html
<!DOCTYPE html>
<html lang="en">
<head>
<meta charset="utf-8">
<title>RV Bone &amp; Vitality Center – Business Card</title>
<link rel="stylesheet" href="https://fonts.googleapis.com/css2?family=Cormorant+SC:wght@600;700&family=Poppins:wght@400;600&family=Roboto+Condensed:wght@700&display=swap">
<style>
  :root {
    --navy: #1b2a50;
    --gold: #c9a35e;
    --gold-light: #ffcc70;
    --gold-deep: #c49c55;
    --ink: #333333;
    --paper: #ffffff;
    --backdrop: #ababab;
  }
  * { margin: 0; padding: 0; box-sizing: border-box; }
  html, body { width: 1093px; height: 1200px; overflow: hidden; }
  body { background: var(--backdrop); position: relative; font-family: "Poppins", sans-serif; }

  .card {
    position: absolute;
    left: 265px;
    background: var(--paper);
    border-radius: 24px;
    overflow: hidden;
  }
  .card--front { top: 226px; width: 577px; height: 356px; }
  .card--back  { top: 621px; width: 581px; height: 357px; }

  .gold-sweep { position: absolute; left: 0; top: 0; width: 577px; height: 356px; }

  .brand-seal {
    position: absolute;
    left: 45px; top: 83px;
    width: 190px; height: 190px;
    border-radius: 50%;
    background: var(--paper);
    border: 1.5px solid var(--gold);
    display: flex; align-items: center; justify-content: center;
    text-align: center;
  }
  .brand-name {
    font-family: "Poppins", sans-serif;
    font-weight: 600;
    color: var(--navy);
    line-height: 1.25;
  }
  .brand-seal .brand-name { font-size: 16px; }

  .name-band {
    position: absolute;
    left: 249px; top: 23px;
    width: 328px; height: 119px;
    background: var(--navy);
    border-radius: 60px 0 0 60px;
    color: var(--paper);
    text-align: right;
    padding: 14px 28px 0 0;
  }
  .doctor-name {
    font-family: "Cormorant SC", serif;
    font-weight: 700;
    font-size: 29px;
    letter-spacing: 0.3px;
    line-height: 1.1;
  }
  .doctor-title {
    margin-top: 8px;
    font-size: 16.5px;
    line-height: 1.28;
  }

  .contact { position: absolute; right: 0; top: 0; width: 577px; height: 356px; }
  .contact-row {
    position: absolute;
    right: 26px;
    display: flex; align-items: center; gap: 7px;
    color: var(--ink);
    font-size: 16.5px;
    line-height: 1.25;
    text-align: right;
    white-space: nowrap;
  }
  .contact-row--address { top: 187px; gap: 10px; }
  .contact-row--phone { top: 252px; }
  .contact-row--fax { top: 278px; }
  .contact-row--email { top: 304px; }
  .icon { width: 25px; height: 25px; flex: none; }

  .back-brand {
    position: absolute;
    left: 0; top: 110px; width: 581px;
    text-align: center;
  }
  .back-brand .brand-name { font-size: 28px; }

  .slogan-rule {
    position: absolute;
    left: 0; top: 309px;
    width: 581px; height: 4px;
    background: var(--gold-deep);
  }
  .slogan {
    position: absolute;
    left: 114px; top: 291px;
    width: 353px; height: 38px;
    border-radius: 19px;
    background: var(--navy);
    display: flex; align-items: center; justify-content: center;
    font-family: "Roboto Condensed", sans-serif;
    font-weight: 700;
    font-size: 21px;
    color: var(--paper);
    white-space: nowrap;
  }
  .slogan-accent { color: var(--gold-deep); margin-left: 5px; }
</style>
</head>
<body>

<section class="card card--front" aria-label="Business card front">
  <svg class="gold-sweep" viewBox="0 0 577 356" aria-hidden="true">
    <defs>
      <radialGradient id="goldGlow" cx="0.15" cy="0.5" r="0.9">
        <stop offset="0" stop-color="#ffcc70"/>
        <stop offset="0.6" stop-color="#e2b564"/>
        <stop offset="1" stop-color="#c49c55"/>
      </radialGradient>
    </defs>
    <path d="M0 0 H171 Q 70 178 169 356 H0 Z" fill="url(#goldGlow)"/>
  </svg>

  <div class="brand-seal">
    <p class="brand-name">RV Bone &amp;<br>Vitality<br>Center</p>
  </div>

  <header class="name-band">
    <h1 class="doctor-name">Lydia Vance, M.D.</h1>
    <p class="doctor-title">Board Certified Hand and Upper<br>Extremity Surgeon</p>
  </header>

  <div class="contact">
    <div class="contact-row contact-row--address">
      <span>38517 North Willowmere Ave<br>Brightwater Cove, FL 33498</span>
      <svg class="icon" viewBox="0 0 25 25" aria-label="Address"><circle cx="12.5" cy="12.5" r="12.5" fill="var(--gold-deep)"/><path d="M12.5 6a4.3 4.3 0 0 0-4.3 4.3c0 3.2 4.3 8 4.3 8s4.3-4.8 4.3-8A4.3 4.3 0 0 0 12.5 6Zm0 5.8a1.5 1.5 0 1 1 0-3 1.5 1.5 0 0 1 0 3Z" fill="#fff"/></svg>
    </div>
    <div class="contact-row contact-row--phone">
      <span>954-218-4063</span>
      <svg class="icon" viewBox="0 0 25 25" aria-label="Phone"><circle cx="12.5" cy="12.5" r="12.5" fill="var(--gold-deep)"/><path d="M8.6 7.2l1.8-.3 1.2 2.7-1.2 1a7 7 0 0 0 3 3l1-1.2 2.7 1.2-.3 1.8c-.1.5-.6.9-1.1.8A9 9 0 0 1 7.8 8.3c-.1-.5.3-1 .8-1.1Z" fill="#fff"/><path d="M14 7.5a3.6 3.6 0 0 1 3.3 3.3M14 5.5a5.6 5.6 0 0 1 5.3 5.3" stroke="#fff" stroke-width="1.1" fill="none" stroke-linecap="round"/></svg>
    </div>
    <div class="contact-row contact-row--fax">
      <span>954-582-7341</span>
      <svg class="icon" viewBox="0 0 25 25" aria-label="Fax"><circle cx="12.5" cy="12.5" r="12.5" fill="var(--gold-deep)"/><rect x="9" y="6" width="7" height="4" fill="none" stroke="#fff" stroke-width="1.3"/><rect x="6.5" y="10" width="12" height="6.5" rx="1.5" fill="none" stroke="#fff" stroke-width="1.3"/><rect x="9" y="14" width="7" height="5" fill="var(--gold-deep)" stroke="#fff" stroke-width="1.3"/></svg>
    </div>
    <div class="contact-row contact-row--email">
      <span>info@myrvbonecare.example</span>
      <svg class="icon" viewBox="0 0 25 25" aria-label="Email"><circle cx="12.5" cy="12.5" r="12.5" fill="var(--gold-deep)"/><rect x="6.5" y="8.5" width="12" height="8.5" fill="none" stroke="#fff" stroke-width="1.3"/><path d="M6.5 8.5l6 5 6-5M6.5 17l4.2-4M18.5 17l-4.2-4" fill="none" stroke="#fff" stroke-width="1.1"/></svg>
    </div>
  </div>
</section>

<section class="card card--back" aria-label="Business card back">
  <div class="back-brand">
    <p class="brand-name">RV Bone &amp;<br>Vitality Center</p>
  </div>
  <div class="slogan-rule"></div>
  <p class="slogan">Grounded in Care.<span class="slogan-accent">Centered on You</span></p>
</section>

</body>
</html>
```